Design of a promotional offer flyer required to promote low-cost websites to 1-man band businesses

I want a flyer designed - either a double-sided A5 flyer or even A4 folded into a third double-sided. The flyer is to showcase a new service - low-cost websites for 1-man-band businesses, business startups and tradesmen in England. Look at the copy, find some pix and let me know! Flyer will be printed and used as an image on my website too. Pix could be related to some of the target groups. We need to stress the simple message that websites start from £5 per week and this is an-all-in-one fee.

Target Market(s)

Tradesmen, business start ups and 1-man band businesses that want a website

Industry/Entity Type

Small Business

Contact Information for Business Card

All contact details and name of business to be confirmed shortly

Font styles to use
Serif

Requirements
Must have
• Basic messages from copy for flyer i.e. websites from £5 per week and what each client gets for that price to be included on the business card! Please read copy for the flyer.
Nice to have
• Nice background image or series of small images relevant to the target audience. Again, see list of targets from copy for flyer.
Should not have
• I don't want exact or similar design to my main business Blue Harbour Promotions. The new flyer and business card should be a different and distinct branding to that of Blue Harbour Promotions. Aimed at a more economical style, whilst looking professional, but relevant to the target audiences.

```html
<!DOCTYPE html>
<html lang="en">
<head>
<meta charset="utf-8">
<title>Solo Trade Websites – Flyer</title>
<link href="https://fonts.googleapis.com/css2?family=Anton&family=Arimo:wght@400;700&family=Lato:wght@400;700&family=Oswald:wght@400;500;700&display=swap" rel="stylesheet">
<style>
:root{
  --red:#e3121b;
  --deep-red:#c8101a;
  --yellow:#fff200;
  --ink:#1a1a1a;
  --grey:#555555;
  --paper:#ffffff;
  --backdrop:#a9a9a9;
  --black:#111111;
}
*{margin:0;padding:0;box-sizing:border-box}
html,body{width:1200px;height:848px;overflow:hidden;background:var(--backdrop)}
.canvas{position:relative;width:1200px;height:848px}
.flyer{position:absolute;top:38px;width:549px;height:770px;background:var(--paper);overflow:hidden;box-shadow:0 2px 8px rgba(0,0,0,.35)}
.flyer--front{left:34px}
.flyer--back{left:609px}
.abs{position:absolute}
.photo{position:absolute}

/* front */
.brand-name{left:34px;top:40px;font:700 34px/1 "Arimo",sans-serif;color:var(--red);z-index:2;white-space:nowrap}
.photo--hero{left:66px;top:30px;width:460px;height:372px;background:radial-gradient(ellipse at 62% 40%,#c69a7e 0%,#e8d6cb 35%,#f3f6fa 62%,#ffffff 80%)}
.headline{left:0;width:549px;text-align:center;top:410px;font:700 44px/1 "Oswald",sans-serif;color:var(--deep-red);letter-spacing:.5px}
.subline{left:0;width:549px;text-align:center;top:458px;font:700 31px/1 "Oswald",sans-serif;color:#4a4a4a}
.price-band{left:0;top:510px;width:549px;height:99px;background:var(--red)}
.price-band__copy{left:40px;top:13px;width:240px;font:400 19px/22px "Oswald",sans-serif;color:#fff;letter-spacing:-.4px}
.price-band__copy b{font-weight:700}
.price-band__rule{left:284px;top:10px;width:2px;height:80px;background:#fff}
.price-band__price{left:300px;top:12px;font:700 42px/1 "Oswald",sans-serif;color:var(--yellow)}
.price-band__upfront{left:300px;top:62px;font:700 25px/1 "Oswald",sans-serif;color:var(--yellow)}
.audience{left:0;top:609px;width:549px;height:81px;background:var(--black);color:#fff;font:400 12.4px/15.2px "Lato",sans-serif;text-align:center;padding:10px 40px 0}
.red-rule{left:0;top:690px;width:549px;height:4px;background:var(--red)}
.address-strip{left:0;top:694px;width:549px;height:35px;font:400 12.3px/35px "Lato",sans-serif;color:#222;text-align:center}
.web-strip{left:0;top:729px;width:549px;height:41px;background:var(--black);color:#fff;font:700 11.5px/40px "Lato",sans-serif;letter-spacing:1.8px;text-align:center}

/* back */
.top-band{left:0;top:0;width:549px;height:26px;background:var(--red)}
.photo--presenter{left:279px;top:34px;width:248px;height:224px;background:radial-gradient(ellipse at 70% 45%,#b98d77 0%,#d9c7c0 30%,#eef0f3 60%,#ffffff 82%)}
.get-title{left:31px;top:42px;font:400 33px/1 "Anton",sans-serif;color:var(--ink);letter-spacing:.3px}
.checklist{left:34px;top:90px;width:510px;list-style:none;font:400 12.4px/15px "Lato",sans-serif;color:#222}
.checklist li{position:relative;padding-left:21px;margin-bottom:5px}
.checklist li svg{position:absolute;left:0;top:2px}
.checklist .narrow{width:210px}
.fee-intro{left:82px;top:384px;font:400 18px/1 "Arimo",sans-serif;color:var(--ink)}
.fee-box{left:0;top:410px;width:335px;height:47px;background:var(--yellow);text-align:center;font:400 15.5px/20px "Lato",sans-serif;color:var(--red);padding-top:4px}
.fee-box span{color:#222}
.photo--devices{left:339px;top:378px;width:190px;height:112px;background:linear-gradient(160deg,#3d4450 0%,#6b7380 45%,#d7dade 100%);border-radius:4px}
.promo-title{left:88px;top:480px;font:700 23px/1 "Arimo",sans-serif;color:var(--red);letter-spacing:1px}
.photo--painter{left:395px;top:506px;width:154px;height:236px;background:linear-gradient(180deg,#f6ece6 0%,#efd9cc 45%,#e9c9b5 100%)}
.promo-box{left:27px;top:514px;width:368px;height:100px;border:2px solid var(--ink);background:#fff;text-align:center}
.promo-box__line{font:500 16px/1 "Oswald",sans-serif;color:var(--ink);margin-top:12px}
.promo-box__line mark{background:var(--yellow);color:var(--red);padding:0 3px}
.promo-box__line--second{margin-top:7px}
.promo-box__cost{font:700 28px/1 "Oswald",sans-serif;color:var(--red);margin-top:9px}
.contact-band{left:0;top:655px;width:394px;height:87px;background:var(--red);color:#fff;text-align:center}
.contact-band__phone{font:700 24px/1 "Oswald",sans-serif;margin:6px 0 3px}
.contact-band__line{font:400 12.5px/16px "Lato",sans-serif}
.contact-band__line b{font-weight:700}
.bottom-band{left:0;top:742px;width:549px;height:28px;background:#2a2a2a}
</style>
</head>
<body>
<div class="canvas">

  <section class="flyer flyer--front">
    <div class="photo photo--hero" role="img" aria-label="Smiling woman pointing at a laptop showing app icons and a phone"></div>
    <div class="abs brand-name">Solo Trade Websites</div>
    <h1 class="abs headline">WANT A WEBSITE</h1>
    <h2 class="abs subline">WITHOUT IT COSTING THE EARTH?</h2>
    <div class="abs price-band">
      <p class="abs price-band__copy">Professionally-designed websites for <b>tradesmen</b>, business start-ups and <b>1-man bands</b> from only</p>
      <div class="abs price-band__rule"></div>
      <div class="abs price-band__price">£5 per week</div>
      <div class="abs price-band__upfront">&amp; NO upfront costs!</div>
    </div>
    <p class="abs audience">Suitable for plumbers, electricians, roofers, builders, painters and decorators, joiners, business start-ups, 1-man bands such as hairdressers, photographers, fitness instructors, window cleaners, beauticians, gardeners, odd job men, wheelie bin cleaners, IFAs or self-employed consultants.</p>
    <div class="abs red-rule"></div>
    <p class="abs address-strip">ADDRESS: 47 Millbrook Lane, Ashbury, AB1 2CD, Lancashire.</p>
    <p class="abs web-strip">www.solotradewebsites.co.uk</p>
  </section>

  <section class="flyer flyer--back">
    <div class="abs top-band"></div>
    <div class="photo photo--presenter" role="img" aria-label="Smiling woman presenting a laptop displaying a website template"></div>
    <h2 class="abs get-title">Here’s what you get :</h2>
    <ul class="abs checklist">
      <li class="narrow"><svg width="13" height="11" viewBox="0 0 13 11"><path d="M1 6l4 4 7-9" fill="none" stroke="#e3121b" stroke-width="2.2"/></svg>Professionally-designed 1-page or 5-page website (Home, About Us, Services, Contact Us, News)</li>
      <li class="narrow"><svg width="13" height="11" viewBox="0 0 13 11"><path d="M1 6l4 4 7-9" fill="none" stroke="#e3121b" stroke-width="2.2"/></svg>Responsive design that displays properly on mobiles and tablets</li>
      <li><svg width="13" height="11" viewBox="0 0 13 11"><path d="M1 6l4 4 7-9" fill="none" stroke="#e3121b" stroke-width="2.2"/></svg>On-going changes and updates</li>
      <li><svg width="13" height="11" viewBox="0 0 13 11"><path d="M1 6l4 4 7-9" fill="none" stroke="#e3121b" stroke-width="2.2"/></svg>All text written for you</li>
      <li><svg width="13" height="11" viewBox="0 0 13 11"><path d="M1 6l4 4 7-9" fill="none" stroke="#e3121b" stroke-width="2.2"/></svg>Photographs (Royalty-free stock images)</li>
      <li><svg width="13" height="11" viewBox="0 0 13 11"><path d="M1 6l4 4 7-9" fill="none" stroke="#e3121b" stroke-width="2.2"/></svg>Professional email addresses e.g. info@yourcompany.co.uk, sales@yourcompany.co.uk and yourname@yourcompany.co.uk. We’ll even set up these email addresses on your PC and laptop!</li>
      <li><svg width="13" height="11" viewBox="0 0 13 11"><path d="M1 6l4 4 7-9" fill="none" stroke="#e3121b" stroke-width="2.2"/></svg>Links to your social media accounts</li>
      <li><svg width="13" height="11" viewBox="0 0 13 11"><path d="M1 6l4 4 7-9" fill="none" stroke="#e3121b" stroke-width="2.2"/></svg>Up to 1 hours’ changes each month to content, pix, and adding new pages</li>
      <li><svg width="13" height="11" viewBox="0 0 13 11"><path d="M1 6l4 4 7-9" fill="none" stroke="#e3121b" stroke-width="2.2"/></svg>Professional hosting for your website and email</li>
      <li><svg width="13" height="11" viewBox="0 0 13 11"><path d="M1 6l4 4 7-9" fill="none" stroke="#e3121b" stroke-width="2.2"/></svg>No upfront cost! Just weekly, monthly or annual invoice - you choose!</li>
    </ul>
    <p class="abs fee-intro">For an all-in fee from</p>
    <p class="abs fee-box">only £5 per week for a 1-page website<br><span>or</span> £10 per week for a 5-page website.</p>
    <div class="photo photo--devices" role="img" aria-label="Website shown on desktop, laptop, tablet and phone screens"></div>
    <h3 class="abs promo-title">Promotional Offer :</h3>
    <div class="photo photo--painter" role="img" aria-label="Decorator painting a wall with a roller"></div>
    <div class="abs promo-box">
      <p class="promo-box__line">Order your new 5-page website <mark>before 31st July 2017</mark></p>
      <p class="promo-box__line promo-box__line--second">and we’ll set up a FriendBook Business Page for FREE.</p>
      <p class="promo-box__cost">Normal Cost: £97 plus VAT!</p>
    </div>
    <div class="abs contact-band">
      <p class="contact-band__phone">Call:&nbsp; 01632 960 418</p>
      <p class="contact-band__line"><b>EMAIL:</b> info@solotradewebsites.co.uk</p>
      <p class="contact-band__line"><b>Address:</b> 47 Millbrook Lane, Ashbury, AB1 2CD, Lancashire.</p>
      <p class="contact-band__line"><b>Visit our web :</b> www.solotradewebsites.co.uk</p>
    </div>
    <div class="abs bottom-band"></div>
  </section>

</div>
</body>
</html>
```